Website Design for The Elder Nook

Please design and code a new website.
Here are the sites I like best:
http://www.voyaglint.com/alternate/
http://www.wheelgiftbay.org
Please make it similar but look at the competitor site (below) for images and wording. This is NOT a car donation site. It's a senior lead placement site like https://www.kinhavenfinder.com. I just like this sites above as a lead generation sites.
Competitor site:
https://www.kinhavenfinder.com (use ideas / verbiage from this site)
Updates
Competitor site:
Coding
Coded - Design and coding required
Number of Pages Required
1 page
Look and feel
Each slider illustrates characteristics of the customer's brand and the style your logo design should communicate.

```html
<!DOCTYPE html>
<html lang="en">
<head>
<meta charset="utf-8">
<title>The Elder Nook – Senior Living Advisors</title>
<link rel="stylesheet" href="https://fonts.googleapis.com/css2?family=Open+Sans:wght@400;600;700;800&display=swap">
<style>
:root{
  --navy:#0c3868;
  --navy-dark:#082a52;
  --green:#1fc592;
  --green-text:#1fb887;
  --ink:#1b2430;
  --muted:#4a5563;
  --light:#f3f5f7;
  --sky:#cfe3f3;
  --white:#ffffff;
}
*{box-sizing:border-box;margin:0;padding:0}
html,body{width:1200px;height:4100px;overflow:hidden;background:var(--white)}
body{font-family:"Open Sans",Arial,sans-serif;color:var(--ink)}
.page{position:relative;width:1200px;height:4100px;overflow:hidden}
section,header,footer,nav{position:absolute;left:0;width:1200px}

/* header */
.site-header{top:0;height:150px;background:var(--white)}
.brand{position:absolute;left:40px;top:34px;display:flex;align-items:center;gap:14px}
.brand-dot{width:46px;height:46px;border-radius:50%;background:var(--green);flex:none}
.brand-name{font-size:34px;font-weight:700;color:var(--navy);line-height:1;white-space:nowrap}
.brand-tag{font-size:11px;font-weight:600;color:var(--muted);letter-spacing:.5px;margin-top:6px;white-space:nowrap}
.header-phone{position:absolute;right:40px;top:38px;display:flex;align-items:center;gap:12px}
.phone-icon{width:58px;height:58px;flex:none}
.phone-num{font-size:34px;font-weight:800;color:var(--navy);line-height:1;white-space:nowrap}
.phone-note{font-size:13px;color:var(--muted);margin-top:4px;white-space:nowrap}

.main-nav{top:150px;height:42px;background:var(--navy);display:flex;align-items:center;padding-left:38px;gap:16px}
.nav-home{width:36px;height:30px;background:var(--green);display:flex;align-items:center;justify-content:center}
.main-nav a{color:var(--white);font-size:12px;font-weight:700;text-decoration:none;text-transform:uppercase;white-space:nowrap}

/* hero */
.hero{top:192px;height:486px;background:linear-gradient(180deg,#7f9a5c 0%,#6e8d4d 45%,#a7b18a 100%)}
.hero-title{position:absolute;left:90px;top:190px;width:600px;text-align:center;color:var(--white);font-size:41px;font-weight:800;line-height:1.2;text-shadow:0 2px 6px rgba(0,0,0,.45)}
.lead-form{position:absolute;left:775px;top:-73px;width:370px;height:505px;background:var(--navy)}
.lead-form h2{height:70px;background:var(--green);color:var(--white);font-size:30px;font-weight:700;text-align:center;line-height:70px}
.form-body{padding:28px 24px}
.field-row{display:flex;gap:10px;margin-bottom:14px}
.field{flex:1;height:52px;background:var(--white);font-size:15px;font-weight:600;color:var(--ink);padding:15px 12px}
.field b{color:#d23b3b}
.field.select{position:relative}
.field.select::after{content:"";position:absolute;right:0;top:0;width:44px;height:52px;background:#e3e6ea}
.submit{display:inline-block;margin-top:12px;background:var(--green);color:var(--white);font-weight:700;font-size:16px;padding:14px 28px}

/* support band */
.support{top:678px;height:220px;background:var(--light)}
.support-label{position:absolute;left:0;top:0;width:520px;height:220px;background:var(--navy);clip-path:polygon(0 0,100% 0,86% 100%,0 100%);padding:48px 0 0 62px;color:var(--white);font-weight:800;font-size:32px;line-height:1.15}
.support-label span{font-size:42px}
.support-items{position:absolute;left:500px;top:55px;display:flex;gap:0}
.support-item{width:140px;text-align:center;font-size:13px;font-weight:700;line-height:1.3;color:var(--ink)}
.support-item svg{display:block;margin:0 auto 14px;width:56px;height:56px}

/* how it works */
.how{top:898px;height:552px}
.section-title{font-size:34px;font-weight:800;color:var(--navy);text-align:center}
.section-title em{font-style:normal;color:var(--green-text)}
.how .section-title{position:absolute;left:0;top:92px;width:820px}
.steps{position:absolute;left:56px;top:170px;display:flex;gap:54px}
.step{width:140px;text-align:center}
.step-photo{width:140px;height:140px;border-radius:50%;border:6px solid var(--white);box-shadow:0 4px 14px rgba(0,0,0,.15);background:radial-gradient(circle at 50% 40%,#d9c6b6,#8b7a6e)}
.step-num{font-size:32px;font-weight:800;color:var(--navy);margin-top:18px}
.step:nth-child(even) .step-num{color:var(--green-text)}
.step-text{font-size:19px;font-weight:600;line-height:1.3;margin-top:4px}
.how-photo{position:absolute;left:820px;top:58px;width:320px;height:494px;background:linear-gradient(180deg,#f2d7d5 0%,#e9c5c5 40%,#dfe2e6 100%)}

/* no cost */
.no-cost{top:1450px;height:437px;background:linear-gradient(180deg,#a9cdee 0%,#d8e8f5 60%,#eef5fb 100%)}
.no-cost-photo{position:absolute;left:0;top:0;width:620px;height:437px;background:linear-gradient(90deg,rgba(255,255,255,.1),rgba(190,214,234,.6))}
.no-cost-copy{position:absolute;left:685px;top:72px;width:480px}
.no-cost-copy h2{font-size:38px;font-weight:800;color:var(--navy)}
.no-cost-copy h2 em{font-style:normal;color:var(--green-text)}
.no-cost-copy p{font-size:17px;font-weight:700;line-height:1.4;margin:18px 0 0 24px;width:420px;text-align:center}
.call-btn{display:inline-block;margin:28px 0 0 40px;background:var(--green);color:var(--white);font-size:32px;font-weight:700;padding:12px 34px;border-radius:4px}

/* testimonials */
.reviews{top:1887px;height:703px}
.reviews .section-title{position:absolute;left:0;top:85px;width:1200px}
.bubble{position:absolute;padding:30px 32px;font-size:16px;line-height:1.55;color:var(--muted);border-radius:8px}
.bubble.one{left:95px;top:175px;width:515px;height:185px;background:#efeaf9}
.bubble.two{left:590px;top:230px;width:520px;height:185px;background:#e7f6fb}
.reviewer{position:absolute;display:flex;align-items:center;gap:22px;font-size:19px;font-weight:700;font-style:italic}
.reviewer.one{left:105px;top:385px}
.reviewer.two{left:605px;top:438px}
.avatar{width:92px;height:92px;border-radius:50%;border:4px solid var(--white);box-shadow:0 3px 10px rgba(0,0,0,.2);background:radial-gradient(circle,#e8d3c4,#a98d7c)}
.dots{position:absolute;left:562px;top:600px;display:flex;gap:8px}
.dots i{width:13px;height:13px;border-radius:50%;border:2px solid #c6cbd2}
.dots i:first-child{background:#c6cbd2}

/* advisor */
.advisor{top:2590px;height:493px;background:linear-gradient(90deg,#f4f1ee 0%,#f4f1ee 38%,#e7ddd6 100%)}
.advisor-photo{position:absolute;left:470px;top:0;width:730px;height:493px;background:linear-gradient(90deg,rgba(244,241,238,0) 0%,#dccfc5 35%,#c9b8ab 100%)}
.advisor-copy{position:absolute;left:86px;top:90px;width:500px}
.advisor-copy h2{font-size:36px;font-weight:800;color:var(--navy);line-height:1.2}
.advisor-copy h2 em{font-style:normal;color:var(--green-text);display:block}
.advisor-copy p{font-size:18px;font-weight:700;line-height:1.45;margin-top:22px}
.perks{list-style:none;margin-top:18px}
.perks li{display:flex;align-items:center;gap:14px;font-size:19px;font-weight:700;color:var(--navy);margin-bottom:14px}
.perks svg{width:28px;height:28px}

/* states */
.states{top:3115px;height:561px}
.states .section-title{position:absolute;left:0;top:55px;width:1200px}
.care-tabs{position:absolute;left:95px;top:140px;width:275px}
.care-tab{display:flex;align-items:center;gap:18px;height:52px;margin-bottom:18px;background:var(--white);box-shadow:0 2px 8px rgba(0,0,0,.12);font-size:19px;font-weight:600;padding-left:8px;position:relative}
.care-tab i{width:38px;height:38px;background:var(--navy);display:block}
.care-tab.active{color:var(--green-text)}
.care-tab.active i{background:var(--green)}
.care-tab.active::after{content:"";position:absolute;right:14px;top:18px;border:8px solid transparent;border-right:10px solid var(--green)}
.state-cols{position:absolute;left:450px;top:143px;display:flex;gap:0}
.state-cols ul{list-style:none;width:225px;font-size:16px;line-height:23px}

/* footer */
.site-footer{top:3676px;height:364px;background:var(--light)}
.footer-photo{position:absolute;left:0;top:0;width:275px;height:364px;background:linear-gradient(180deg,#e6e3df,#b9aca3)}
.footer-col{position:absolute;top:65px}
.footer-col h3{font-size:15px;font-weight:800;color:var(--green-text);text-transform:uppercase;padding-bottom:12px;border-bottom:1px solid #cfd4da}
.footer-col p,.footer-col li{font-size:13px;line-height:1.5;color:var(--ink);margin-top:14px;white-space:nowrap}
.footer-col ul{list-style:none;margin-top:14px}
.footer-col ul li{margin-top:0}
.about{left:300px}
.about h3{width:260px}
.links{left:623px}
.links h3{width:145px}
.footer-brand{position:absolute;left:790px;top:0;width:410px;height:364px;background:var(--navy);clip-path:polygon(12% 0,100% 0,100% 100%,0 100%,0 22%);color:var(--white)}
.footer-logo{position:absolute;left:90px;top:48px;display:flex;align-items:center;gap:12px}
.footer-logo .brand-dot{width:40px;height:40px}
.footer-logo .brand-name{color:var(--white);font-size:30px}
.footer-logo .brand-tag{color:var(--white);font-size:10px}
.socials{position:absolute;left:170px;top:132px;display:flex;gap:8px}
.socials i{width:28px;height:28px;border:2px solid var(--white);border-radius:50%}
.footer-phone{position:absolute;left:70px;top:230px;display:flex;align-items:center;gap:12px}
.footer-phone .phone-num{color:var(--white);font-size:30px}
.footer-phone .phone-note{color:var(--white)}
.copyright{position:absolute;left:0;top:4040px;width:1200px;height:60px;line-height:60px;text-align:center;font-size:13px;font-weight:700;background:var(--white);text-transform:uppercase}
</style>
</head>
<body>
<div class="page">

<header class="site-header">
  <div class="brand">
    <span class="brand-dot"></span>
    <div><div class="brand-name">The Elder Nook</div><div class="brand-tag">CONNECTING FAMILIES TO SENIOR LIVING</div></div>
  </div>
  <div class="header-phone">
    <svg class="phone-icon" viewBox="0 0 58 58"><circle cx="29" cy="29" r="26" fill="none" stroke="#0c3868" stroke-width="4"/><path d="M20 17c2-1 4 0 5 2l2 5c0 2-1 3-2 4 1 3 4 6 7 7 1-1 2-2 4-2l5 2c2 1 3 3 2 5-2 3-5 4-8 3-8-3-13-8-16-16-1-3 0-7 1-10z" fill="#0c3868"/></svg>
    <div><div class="phone-num">1-800-555-0142</div><div class="phone-note">Talk Today to a Local Advisor for FREE</div></div>
  </div>
</header>

<nav class="main-nav">
  <span class="nav-home"><svg width="18" height="16" viewBox="0 0 18 16"><path d="M9 0l9 8h-3v8H11v-5H7v5H3V8H0z" fill="#fff"/></svg></span>
  <a href="#">Assisted Living</a><a href="#">Memory Care</a><a href="#">Nursing Homes</a><a href="#">More Living Options ▾</a><a href="#">Planning &amp; Advice</a>
</nav>

<section class="hero" role="img" aria-label="Older couple walking arm in arm on a green lawn beside a wheelchair">
  <h1 class="hero-title">You know your family.<br>We know Senior Living.<br>Find Senior Living Near You.</h1>
  <form class="lead-form">
    <h2>Contact us now!</h2>
    <div class="form-body">
      <div class="field-row"><div class="field">First Name<b>*</b></div><div class="field">Last Name<b>*</b></div></div>
      <div class="field-row"><div class="field">Primary Phone<b>*</b></div><div class="field">Cell Phone<b>*</b></div></div>
      <div class="field-row"><div class="field">Email Address<b>*</b></div></div>
      <div class="field-row"><div class="field select">State<b>*</b></div></div>
      <span class="submit">SUBMIT</span>
    </div>
  </form>
</section>

<section class="support">
  <div class="support-label">THE SUPPORT YOU<br>NEED TO MAKE THE<br><span>RIGHT CHOICE</span></div>
  <div class="support-items">
    <div class="support-item"><svg viewBox="0 0 56 56"><circle cx="22" cy="16" r="9" fill="none" stroke="#1fc592" stroke-width="4"/><path d="M6 48c0-10 7-17 16-17s16 7 16 17" fill="none" stroke="#0c3868" stroke-width="4"/><circle cx="44" cy="40" r="7" fill="#1fc592"/></svg>Dedicated local advisor</div>
    <div class="support-item"><svg viewBox="0 0 56 56"><path d="M6 50V24l14-10 14 10v26z" fill="none" stroke="#0c3868" stroke-width="4"/><rect x="34" y="30" width="16" height="20" fill="none" stroke="#1fc592" stroke-width="4"/><rect x="16" y="36" width="8" height="14" fill="#1fc592"/></svg>Hand-picked list of communities to match your needs</div>
    <div class="support-item"><svg viewBox="0 0 56 56"><rect x="10" y="4" width="36" height="48" rx="3" fill="none" stroke="#1fc592" stroke-width="4"/><path d="M28 14v28M22 20h10a4 4 0 0 1 0 8h-8a4 4 0 0 0 0 8h10" fill="none" stroke="#0c3868" stroke-width="3"/></svg>Full details and pricing</div>
    <div class="support-item"><svg viewBox="0 0 56 56"><rect x="6" y="10" width="44" height="40" rx="3" fill="none" stroke="#0c3868" stroke-width="4"/><path d="M6 20h44M16 4v10M40 4v10" stroke="#0c3868" stroke-width="4"/><path d="M15 28h6M25 28h6M35 28h6M15 38h6M25 38h6" stroke="#1fc592" stroke-width="4"/></svg>Help scheduling tours</div>
    <div class="support-item"><svg viewBox="0 0 56 56"><path d="M4 36l6-14h30l10 10v6H4z" fill="none" stroke="#1fc592" stroke-width="4"/><circle cx="16" cy="40" r="5" fill="#0c3868"/><circle cx="40" cy="40" r="5" fill="#0c3868"/></svg>Move in support</div>
  </div>
</section>

<section class="how">
  <h2 class="section-title">How Our <em>Service Works</em></h2>
  <div class="steps">
    <div class="step"><div class="step-photo" role="img" aria-label="Advisor wearing a headset"></div><div class="step-num">01.</div><div class="step-text">Talk with your local advisor</div></div>
    <div class="step"><div class="step-photo" role="img" aria-label="Woman reviewing care options"></div><div class="step-num">02.</div><div class="step-text">Get information on care options</div></div>
    <div class="step"><div class="step-photo" role="img" aria-label="Family visiting a senior community"></div><div class="step-num">03.</div><div class="step-text">Select the communities to visit</div></div>
    <div class="step"><div class="step-photo" role="img" aria-label="Senior settling into a new home"></div><div class="step-num">04.</div><div class="step-text">Transition to new home</div></div>
  </div>
  <div class="how-photo" role="img" aria-label="Young woman helping an older man using a walker"></div>
</section>

<section class="no-cost">
  <div class="no-cost-photo" role="img" aria-label="Older man with arms stretched wide under a blue sky"></div>
  <div class="no-cost-copy">
    <h2>There's <em>No Cost</em> to You</h2>
    <p>We work with over 20,000 senior living communities. Our community partners pay us for placement services.</p>
    <span class="call-btn">Call 800-555-0142</span>
  </div>
</section>

<section class="reviews">
  <h2 class="section-title">97% of Our Customers <em>Recommend Our Service</em></h2>
  <div class="bubble one">Lorem ipsum dolor sit amet, consectetur adipiscing elit, sed do eiusmod tempor incididunt ut labore et dolore magna aliqua. Ut enim ad minim veniam, quis nostrud exercitation ullamco laboris nisi ut aliquip ex. Duis aute irure dolor in reprehenderit in voluptate velit esse.</div>
  <div class="bubble two">Lorem ipsum dolor sit amet, consectetur adipiscing elit, sed do eiusmod tempor incididunt ut labore et dolore magna aliqua. Ut enim ad minim veniam, quis nostrud exercitation ullamco laboris nisi ut aliquip ex. Duis aute irure dolor in reprehenderit in voluptate velit esse.</div>
  <div class="reviewer one"><span class="avatar" role="img" aria-label="Portrait of reviewer"></span>Maren Holloway</div>
  <div class="reviewer two"><span class="avatar" role="img" aria-label="Portrait of reviewer"></span>Tessa Brightwell</div>
  <div class="dots"><i></i><i></i><i></i><i></i></div>
</section>

<section class="advisor">
  <div class="advisor-photo" role="img" aria-label="Smiling older woman with a caregiver at her shoulder"></div>
  <div class="advisor-copy">
    <h2>Your local advisor.<em>You decide.</em></h2>
    <p>Over 400 senior advisors across the U.S. and Canada are ready to help your family with:</p>
    <ul class="perks">
      <li><svg viewBox="0 0 28 28"><path d="M14 2a9 9 0 0 0-9 9c0 7 9 15 9 15s9-8 9-15a9 9 0 0 0-9-9z" fill="none" stroke="#0c3868" stroke-width="2.5"/><circle cx="14" cy="11" r="3" fill="#0c3868"/></svg>Insider's tips for the area near you</li>
      <li><svg viewBox="0 0 28 28"><circle cx="10" cy="9" r="5" fill="none" stroke="#0c3868" stroke-width="2.5"/><path d="M2 26c0-6 4-9 8-9s8 3 8 9M18 6h8M18 11h6" fill="none" stroke="#0c3868" stroke-width="2.5"/></svg>Advice tailored to your unique situation</li>
      <li><svg viewBox="0 0 28 28"><circle cx="14" cy="14" r="12" fill="none" stroke="#0c3868" stroke-width="2.5"/><path d="M14 12v9" stroke="#0c3868" stroke-width="3"/><circle cx="14" cy="8" r="1.8" fill="#0c3868"/></svg>Time saving know-how and resources</li>
    </ul>
  </div>
</section>

<section class="states">
  <h2 class="section-title">Senior living <em>by state</em></h2>
  <div class="care-tabs">
    <div class="care-tab active"><i></i>Assisted Living</div>
    <div class="care-tab"><i></i>Memory Care</div>
    <div class="care-tab"><i></i>Independent Living</div>
    <div class="care-tab"><i></i>Nursing Home</div>
    <div class="care-tab"><i></i>Care Homes</div>
  </div>
  <div class="state-cols">
    <ul><li>Alabama</li><li>Arizona</li><li>Arkansas</li><li>California</li><li>Colorado</li><li>Connecticut</li><li>Delaware</li><li>District of Columbia</li><li>Florida</li><li>Georgia</li><li>Hawaii</li><li>Idaho</li><li>Illinois</li><li>Indiana</li><li>Iowa</li><li>Kansas</li><li>Kentucky</li></ul>
    <ul><li>Louisiana</li><li>Maine</li><li>Maryland</li><li>Massachusetts</li><li>Michigan</li><li>Minnesota</li><li>Mississippi</li><li>Missouri</li><li>Montana</li><li>Nebraska</li><li>Nevada</li><li>New Hampshire</li><li>New Jersey</li><li>New Mexico</li><li>New York</li><li>North Carolina</li><li>North Dakota</li></ul>
    <ul><li>Ohio</li><li>Oklahoma</li><li>Oregon</li><li>Pennsylvania</li><li>Rhode Island</li><li>South Carolina</li><li>South Dakota</li><li>Tennessee</li><li>Texas</li><li>Utah</li><li>Vermont</li><li>Virginia</li><li>Washington</li><li>West Virginia</li><li>Wisconsin</li><li>Wyoming</li></ul>
  </div>
</section>

<footer class="site-footer">
  <div class="footer-photo" role="img" aria-label="Smiling older man with glasses and crossed arms"></div>
  <div class="footer-col about">
    <h3>About The Elder Nook</h3>
    <p>Lorem ipsum dolor sit amet, consectetur<br>adipiscing elit, sed diam nonummy nibh<br>euismod tincidunt ut laoreet dolore magna<br>aliquam erat volutpat. Ut wisi enim ad minim<br>veniam, quis nostrud exerci tation ullamcor<br>per suscipit lobortis nisl ut.</p>
  </div>
  <div class="footer-col links">
    <h3>Quick Links</h3>
    <ul><li>Assisted Living</li><li>Memory Care</li><li>Nursing Home</li><li>More Living Options</li><li>Planning &amp; Advice</li><li>How Our Service Works</li></ul>
  </div>
  <div class="footer-brand">
    <div class="footer-logo"><span class="brand-dot"></span><div><div class="brand-name">The Elder Nook</div><div class="brand-tag">CONNECTING FAMILIES TO SENIOR LIVING</div></div></div>
    <div class="socials"><i></i><i></i><i></i></div>
    <div class="footer-phone">
      <svg class="phone-icon" viewBox="0 0 58 58"><circle cx="29" cy="29" r="26" fill="none" stroke="#fff" stroke-width="4"/><path d="M20 17c2-1 4 0 5 2l2 5c0 2-1 3-2 4 1 3 4 6 7 7 1-1 2-2 4-2l5 2c2 1 3 3 2 5-2 3-5 4-8 3-8-3-13-8-16-16-1-3 0-7 1-10z" fill="#fff"/></svg>
      <div><div class="phone-num">1-800-555-0142</div><div class="phone-note">Talk Today to a Local Advisor for FREE</div></div>
    </div>
  </div>
</footer>
<div class="copyright">Copyright © 2019 The Elder Nook. All rights reserved.</div>

</div>
</body>
</html>
```